Mobile app for checking bus arrival

I would like to make the UI much more beautiful and modern. The app is an app to check bus arrival in Singapore.
See here: https://apps.veltrano.com/store/apps/details?id=com.ridoka&hl=en

Based on the question from designers:

1. The first screen shows the favorite bus stop. Each item shows location / street, the top one is the location, second line is the street name. And the number is the bus stop code.

2. Please download the app and try bus stop code with 07589 or 10079, for example. It will bring you to the next screen.

3. The pencil allow you to select color theme, for the list item, and the header.

4. On the second screen, it will show up the list of bus route that available on that bus stop.

5. When you tap on one of them it will show you the 2 subsequent arrival time.

6. Each of the arrival time has the information of availability seats available, seats not available, no more space. (we can use green, yellow, red, respectively).

7. Each of the arrival time has the WAB indicator (Wheelchair availability). Show as icon is preferred.

7. KLT and VOPN are the bus provider in Singapore. 48 means the route /service no.

Requirements:
And check the attachment, see screen 3. I need to add information about the space availability, which has 3 state: seats available, seats not available, no more space. (we can use green, yellow, red, respectively).

Please advise how to show the information.

Target Market(s)

Students, age below 35

Industry/Entity Type

Trivex

Requirements
Must have
• The app currently has the capabilities to select color theme, checkout screen1. It's the button and the list item color.
Nice to have
• Please download the app to see all available colors, and make suggestion to have better color pallete.

```html
<!DOCTYPE html>
<html lang="en">
<head>
<meta charset="utf-8">
<title>Bus Arrival – Menu</title>
<link rel="stylesheet" href="https://fonts.googleapis.com/css2?family=Inter:wght@400;500&family=Open+Sans:wght@400&family=Source+Sans+3:wght@300;400&display=swap">
<style>
  :root {
    --brand-blue: #527ef5;
    --header-accent: #4a6ee0;
    --card-blue: #6b8cf5;
    --drawer-bg: #2f3447;
    --drawer-active: #2a2e3f;
    --drawer-text: #a9adbb;
    --white: #ffffff;
    --divider: #e4e6ee;
  }
  * { box-sizing: border-box; margin: 0; padding: 0; }
  html, body { width: 676px; height: 1200px; overflow: hidden; }
  body { background: var(--drawer-bg); position: relative; font-family: "Source Sans 3", sans-serif; }

  .status-bar {
    position: absolute; left: 0; top: 0; width: 676px; height: 51px;
    background: var(--brand-blue); color: var(--white);
    font-family: "Inter", sans-serif; font-size: 22px;
  }
  .status-bar .carrier { position: absolute; left: 10px; top: 12px; display: flex; align-items: center; gap: 6px; }
  .status-bar .time { position: absolute; left: 0; right: 0; top: 12px; text-align: center; font-weight: 500; }
  .status-bar .power { position: absolute; right: 12px; top: 12px; display: flex; align-items: center; gap: 10px; }

  .drawer-menu { position: absolute; left: 0; top: 158px; width: 550px; list-style: none; }
  .drawer-item {
    position: absolute; left: 6px; width: 544px; height: 112px;
    display: flex; align-items: center; color: var(--drawer-text);
    font-size: 28px; font-weight: 300;
  }
  .drawer-item svg { position: absolute; left: 38px; width: 44px; height: 44px; }
  .drawer-item span { position: absolute; left: 115px; }
  .drawer-item.is-active { background: var(--drawer-active); }

  .main-screen { position: absolute; left: 550px; top: 158px; width: 126px; height: 1042px; background: var(--white); overflow: hidden; }
  .app-header { position: absolute; left: 0; top: 0; width: 126px; height: 93px; background: var(--brand-blue); }
  .app-header .menu-toggle { position: absolute; left: 35px; top: 30px; }
  .app-header .header-field { position: absolute; left: 98px; top: 17px; width: 60px; height: 64px; background: var(--header-accent); }

  .stop-card {
    position: absolute; left: 34px; width: 140px; height: 94px;
    background: var(--card-blue); border-radius: 8px;
    color: var(--white); font-family: "Open Sans", sans-serif; font-size: 23px;
    display: flex; align-items: center; padding-left: 17px;
  }
  .list-end { position: absolute; left: 0; top: 697px; width: 126px; height: 1px; background: var(--divider); }
</style>
</head>
<body>
  <header class="status-bar">
    <div class="carrier">
      <svg width="78" height="14" viewBox="0 0 78 14" aria-hidden="true">
        <g fill="#fff" stroke="#fff" stroke-width="1.5">
          <circle cx="7" cy="7" r="5.5"/><circle cx="22" cy="7" r="5.5"/><circle cx="37" cy="7" r="5.5"/>
          <circle cx="52" cy="7" r="5.5" fill="none"/><circle cx="67" cy="7" r="5.5" fill="none"/>
        </g>
      </svg>
      <span>VELO</span>
      <svg width="24" height="18" viewBox="0 0 24 18" aria-hidden="true">
        <g fill="none" stroke="#fff" stroke-width="2.4" stroke-linecap="round">
          <path d="M2 6 A14 14 0 0 1 22 6"/><path d="M6 10 A8 8 0 0 1 18 10"/>
        </g>
        <circle cx="12" cy="15" r="2.4" fill="#fff"/>
      </svg>
    </div>
    <div class="time">4:21 PM</div>
    <div class="power">
      <svg width="14" height="24" viewBox="0 0 14 24" aria-hidden="true">
        <path d="M2 7 L12 17 L7 22 V2 L12 7 L2 17" fill="none" stroke="#c8d6ff" stroke-width="1.6"/>
      </svg>
      <span>22%</span>
      <svg width="50" height="22" viewBox="0 0 50 22" aria-hidden="true">
        <rect x="1" y="1" width="43" height="20" rx="3" fill="none" stroke="#fff" stroke-width="1.6"/>
        <rect x="4" y="4" width="9" height="14" fill="#fff"/>
        <rect x="45.5" y="7" width="3" height="8" rx="1" fill="#fff"/>
      </svg>
    </div>
  </header>

  <nav>
    <ul class="drawer-menu">
      <li class="drawer-item" style="top:0px">
        <svg viewBox="0 0 44 44" aria-hidden="true" fill="none" stroke="currentColor" stroke-width="2">
          <rect x="7" y="6" width="30" height="36" rx="2"/><rect x="15" y="2" width="14" height="7" rx="1"/>
          <path d="M12 18 l2 2 4-4 M12 26 l2 2 4-4 M12 34 l2 2 4-4 M22 18 h10 M22 26 h10 M22 34 h10"/>
        </svg>
        <span>Backup Favorite List</span>
      </li>
      <li class="drawer-item" style="top:110px">
        <svg viewBox="0 0 44 44" aria-hidden="true">
          <circle cx="20" cy="21" r="17" fill="currentColor"/>
          <path d="M8 14 q8 4 6 10 q-3 5 2 10 M24 6 q-2 8 6 9 q6 0 6 6" fill="none" stroke="var(--drawer-bg)" stroke-width="2.5"/>
          <path d="M24 22 L42 30 L34 32 L38 40 L35 42 L31 34 L26 38 Z" fill="currentColor" stroke="var(--drawer-bg)" stroke-width="2"/>
        </svg>
        <span>Browse Free Apps</span>
      </li>
      <li class="drawer-item is-active" style="top:223px">
        <svg viewBox="0 0 44 44" aria-hidden="true" fill="none" stroke="currentColor" stroke-width="2">
          <path d="M19 4 h6 l1 5 4 2 4-3 4 4 -3 4 2 4 5 1 v6 l-5 1 -2 4 3 4 -4 4 -4-3 -4 2 -1 5 h-6 l-1-5 -4-2 -4 3 -4-4 3-4 -2-4 -5-1 v-6 l5-1 2-4 -3-4 4-4 4 3 4-2 z"/>
          <circle cx="22" cy="22" r="7"/>
        </svg>
        <span>Settings</span>
      </li>
      <li class="drawer-item" style="top:336px">
        <svg viewBox="0 0 44 44" aria-hidden="true" fill="none" stroke="currentColor" stroke-width="2">
          <circle cx="22" cy="22" r="19"/><circle cx="22" cy="22" r="14"/>
          <path d="M26 16 q-1-3 -4-3 q-5 0 -5 4 q0 3 5 4 q5 1 5 4 q0 4 -5 4 q-4 0 -5-3 M22 10 v3 M22 31 v3"/>
        </svg>
        <span>Simple Budget</span>
      </li>
    </ul>
  </nav>

  <main class="main-screen">
    <div class="app-header">
      <svg class="menu-toggle" width="36" height="36" viewBox="0 0 36 36" aria-label="Menu" role="img">
        <g stroke="#fff" stroke-width="2.5"><path d="M0 2 H36 M0 19 H36 M0 36 H36"/></g>
      </svg>
      <div class="header-field"></div>
    </div>
    <div class="stop-card" style="top:115px">09022</div>
    <div class="stop-card" style="top:236px">10079</div>
    <div class="stop-card" style="top:359px">18141</div>
    <div class="stop-card" style="top:481px">66081</div>
    <div class="stop-card" style="top:601px">08031</div>
    <div class="list-end"></div>
  </main>
</body>
</html>
```